We are a physical therapy billing company. We need a postcard style flyer.

See attached. We are trying to generate more business for our physical therapy billing company. Our company name is Motion Claims Partners.

Industry/Entity Type

Physical Therapy

```html
<!DOCTYPE html>
<html lang="en">
<head>
<meta charset="utf-8">
<title>Motion Claims Partners – Postcard</title>
<link href="https://fonts.googleapis.com/css2?family=Roboto+Slab:wght@800;900&family=Roboto:wght@300;400;700;900&family=Roboto+Condensed:wght@400;700&family=Tinos&display=swap" rel="stylesheet">
<style>
  :root {
    --green: #5ee42a;
    --green-deep: #3fbf1d;
    --blue: #2f8de4;
    --blue-text: #2a8ae0;
    --ink: #1a1a1a;
    --dark: #121212;
    --white: #ffffff;
    --grey: #8a8a8a;
    --line: #555555;
    --stage: #e7e4df;
  }
  * { margin: 0; padding: 0; box-sizing: border-box; }
  html, body { width: 779px; height: 1200px; overflow: hidden; }
  body { background: var(--stage); position: relative; font-family: "Roboto", Arial, sans-serif; }

  .card { position: absolute; box-shadow: 0 6px 18px rgba(0,0,0,.25); overflow: hidden; }

  /* Front */
  .front { left: 65px; top: 73px; width: 648px; height: 498px; background: var(--white); }
  .front-hero { position: absolute; left: 0; top: 0; width: 648px; height: 382px; background: var(--dark); }
  .hero-photo { position: absolute; left: 0; top: 0; width: 380px; height: 382px;
    background: linear-gradient(90deg, #3a3633 0%, #5a4a42 40%, #2a2522 75%, var(--dark) 100%); }
  .headline { position: absolute; left: 346px; top: 52px; width: 300px; text-align: center;
    font-family: "Roboto Slab", Georgia, serif; font-weight: 900; color: var(--green);
    font-size: 57px; line-height: 56px; letter-spacing: 1px; }
  .subhead { position: absolute; left: 346px; top: 178px; width: 300px; text-align: center;
    font-family: "Roboto Slab", Georgia, serif; font-weight: 800; color: var(--white);
    font-size: 19px; line-height: 23px; }
  .subhead em { font-style: normal; color: var(--green); }
  .guarantee { position: absolute; left: 338px; top: 276px; width: 320px; text-align: center;
    font-weight: 700; color: var(--white); font-size: 14.5px; line-height: 18px; }
  .contact-band { position: absolute; left: 0; top: 382px; width: 648px; height: 38px; background: var(--blue); }
  .contact-band p { position: absolute; left: 315px; top: 5px; color: var(--white); font-weight: 300; font-size: 23px; }
  .contact-band strong { font-weight: 700; }
  .brand-mark { position: absolute; left: 52px; top: 365px; display: flex; align-items: center; gap: 8px; }
  .brand-mark .dot { width: 22px; height: 22px; border-radius: 50%; background: var(--green-deep); }
  .brand-mark span { font-weight: 900; font-size: 34px; color: var(--green-deep); letter-spacing: 2px; }
  .front-company { position: absolute; left: 33px; top: 461px; color: var(--blue-text); font-weight: 700; font-size: 12.5px; }
  .front-web { position: absolute; left: 302px; top: 432px; color: var(--blue-text); font-weight: 700; font-size: 15px; }
  .front-phone { position: absolute; left: 317px; top: 452px; color: var(--green-deep); font-weight: 700; font-size: 25px; }

  /* Back */
  .back { left: 61px; top: 631px; width: 656px; height: 505px; background: var(--white); }
  .why { position: absolute; left: 21px; top: 22px; color: var(--blue-text); font-weight: 700; font-size: 18px; }
  .pitch { position: absolute; left: 21px; top: 55px; width: 295px; font-size: 11.3px; line-height: 13.4px;
    color: var(--ink); text-align: justify; }
  .pitch p { margin-bottom: 13px; }
  .pitch b { color: var(--green-deep); font-weight: 900; }
  .back-mark { position: absolute; left: 348px; top: 26px; display: flex; align-items: center; gap: 6px; }
  .back-mark .dot { width: 14px; height: 14px; border-radius: 50%; background: var(--green-deep); }
  .back-mark span { font-weight: 900; font-size: 22px; color: var(--green-deep); letter-spacing: 1px; }
  .sender { position: absolute; left: 346px; top: 78px; font-family: "Roboto Condensed", Arial, sans-serif;
    font-size: 11.5px; line-height: 14px; color: var(--ink); }
  .sender .name { font-weight: 700; font-size: 12.5px; margin-bottom: 3px; }
  .sender .gap { margin-top: 6px; }
  .label { position: absolute; font-family: "Tinos", Georgia, serif; color: var(--grey); font-size: 12.5px; }
  .postage-box { position: absolute; left: 553px; top: 30px; width: 69px; height: 80px; border: 1px solid var(--line); }
  .address-line { position: absolute; left: 372px; width: 215px; height: 1px; background: var(--line); }
</style>
</head>
<body>

<section class="card front">
  <div class="front-hero">
    <div class="hero-photo" role="img" aria-label="Photo of a stressed man holding his head as crumpled billing papers fly out of it"></div>
    <h1 class="headline">BILLING<br>ISSUES?</h1>
    <p class="subhead">LET <em>MOTION CLAIMS<br>PARTNERS</em> RELIEVE<br>THOSE HEADACHES.</p>
    <p class="guarantee">WE GUARANTEE AN INCREASE<br>IN YOUR COLLECTIONS<br>AND A DECREASE IN YOUR<br>ACCOUNTS RECEIVABLE.</p>
  </div>
  <div class="contact-band"><p>CONTACT <strong>MCP</strong> TODAY AT</p></div>
  <div class="brand-mark"><i class="dot"></i><span>MCP</span></div>
  <p class="front-company">MOTION CLAIMS PARTNERS LLC</p>
  <p class="front-web">MOTIONCLAIMSPARTNERS.COM</p>
  <p class="front-phone">CALL : 301-555-0148</p>
</section>

<section class="card back">
  <h2 class="why">Why MCP?</h2>
  <div class="pitch">
    <p><b>KNOWLEDGE :</b> Our billers are trained exclusively in physical therapy billing and collections. MCP will work with the billing system you choose or are currently using. In addition, with one of our owners being a physical therapist herself, MCP has first-hand knowledge in choosing a PT software program that meets documentation standards and maximizes your collections.</p>
    <p><b>EXPERIENCE :</b> MCP is a physical therapy billing and consulting company with over 25 years of experience in managing physical therapy practices. We are experts in documentation and coding practices, and our billers are trained in Medicare and private payer guidelines and modifiers. MCP has the skills necessary to increase the efficiency and profitability of your clinic by taking the stress of billing and collections away from your staff, and allowing them to do what they do best – take care of patients!</p>
    <p><b>ANCILLARY INCOME :</b> MCP can also improve your revenue by showing you how to develop additional services beyond standard physical therapy. We can develop a bracing and custom orthotics program for your clinic that enhances patient care and provides additional sources of revenue in a competitive marketplace.</p>
  </div>

  <div class="back-mark"><i class="dot"></i><span>MCP</span></div>
  <div class="sender">
    <p class="name">Motion Claims Partners LLC</p>
    <p>4120 Larkspur Avenue,<br>Ashbury, MD 20900.</p>
    <p class="gap"><b>Phone:</b> 1-240-555-0172<br><b>Email:</b> info@motionclaimspartners.com</p>
  </div>

  <span class="label" style="left:546px;top:11px;">Postage Area</span>
  <div class="postage-box"></div>
  <span class="label" style="left:432px;top:216px;">Address Area</span>
  <div class="address-line" style="top:240px;"></div>
  <div class="address-line" style="top:279px;"></div>
  <div class="address-line" style="top:318px;"></div>
  <span class="label" style="left:367px;top:467px;">Barcode Area</span>
</section>

</body>
</html>
```